Facial Tissue Brand Logo and Design

We would like you to design a Logo for the Facial Tissue Brand "Velora" along with the box design. The pack should indicate the pack size (150 x 2 ply). Also our company logo should be present (attached) along with a barcode. The box size dimensions should be 210mm (L) x 110mm (W) x 70mm (H). We are open to all kinds of nice designs which are attractive but not overdone. Happy designing!

UPDATE:
We appreciate the designs so far... but would also love to see more options in a simple and elegent design style that would look good on a table... please see attached below links for reference purpose:

www.pictovault-example.com/image-photo/cleaning-wipes-isolated-on-white-257770819

www.pictovault-example.com/image-photo/cleaning-wipes-isolated-on-white-155326937

www.pictovault-example.com/image-photo/delicate-female-hands-pulling-tissue-out-1330426586

Happy desgining!

We appreciate the designs so far.. but would like to to see some more options.

```html
<!DOCTYPE html>
<html lang="en">
<head>
<meta charset="utf-8">
<title>Velora Facial Tissue – Box Dieline</title>
<link rel="stylesheet" href="https://fonts.googleapis.com/css2?family=Playfair+Display:wght@700&family=Great+Vibes&display=swap">
<style>
  :root {
    --page: #ffffff;
    --blush: #f3c3cb;
    --cream: #f1ede6;
    --cut-line: #5a5a5a;
    --label: #ffffff;
    --brand-teal: #159f89;
    --accent-pink: #e2779f;
  }
  html, body {
    margin: 0;
    padding: 0;
    width: 1200px;
    height: 800px;
    overflow: hidden;
    background: var(--page);
  }
  .dieline {
    display: block;
    width: 1200px;
    height: 800px;
  }
  .panel-blush { fill: var(--blush); }
  .panel-cream { fill: var(--cream); }
  .cut-outline { fill: none; stroke: var(--cut-line); stroke-width: 1.6; }
  .fold-line { stroke: var(--cut-line); stroke-width: 1.2; }
  .brand-label { fill: var(--label); }
  .brand-name {
    font-family: "Playfair Display", Georgia, serif;
    font-weight: 700;
    fill: var(--brand-teal);
  }
  .brand-descriptor {
    font-family: "Great Vibes", cursive;
    fill: var(--accent-pink);
  }
</style>
</head>
<body>
<svg class="dieline" viewBox="-513 0 2355 1570" preserveAspectRatio="xMidYMid meet" xmlns="http://www.w3.org/2000/svg" aria-label="Velora facial tissue box dieline">
  <defs>
    <clipPath id="box-shape">
      <!-- top panel and flaps -->
      <polygon points="222,92 275,92 1055,92 1105,92 1173,118 1173,330 1105,352 222,352 155,330 155,115"/>
      <!-- front panel and side flaps -->
      <path d="M275,352 L262,360 L95,370 Q85,372 85,382 L85,736 Q85,746 95,747 L262,752 L275,760 L1055,760 L1068,752 L1235,747 Q1245,746 1245,736 L1245,382 Q1245,372 1235,370 L1068,360 L1055,352 Z"/>
      <!-- bottom panel and flaps -->
      <polygon points="222,760 1105,760 1173,785 1173,998 1105,1020 222,1020 155,998 155,785"/>
      <!-- back panel with notched flaps -->
      <polygon points="275,1020 1055,1020 1162,1058 1162,1128 1235,1128 1245,1140 1245,1310 1235,1320 1162,1320 1162,1390 1055,1430 275,1430 165,1390 165,1320 95,1320 85,1310 85,1140 95,1128 165,1128 165,1058"/>
      <!-- tuck tab -->
      <polygon points="275,1430 1055,1430 1038,1477 290,1477"/>
    </clipPath>
  </defs>

  <g class="box-artwork" clip-path="url(#box-shape)" role="img" aria-label="Soft interlocking circle pattern on blush and cream background">
    <rect class="panel-blush" x="80" y="90" width="393" height="1390"/>
    <rect class="panel-cream" x="473" y="90" width="780" height="1390"/>
  </g>

  <g class="cut-lines">
    <polygon class="cut-outline" points="222,92 1105,92 1173,118 1173,330 1105,352 222,352 155,330 155,115"/>
    <path class="cut-outline" d="M275,352 L262,360 L95,370 Q85,372 85,382 L85,736 Q85,746 95,747 L262,752 L275,760 L1055,760 L1068,752 L1235,747 Q1245,746 1245,736 L1245,382 Q1245,372 1235,370 L1068,360 L1055,352 Z"/>
    <polygon class="cut-outline" points="222,760 1105,760 1173,785 1173,998 1105,1020 222,1020 155,998 155,785"/>
    <polygon class="cut-outline" points="275,1020 1055,1020 1162,1058 1162,1128 1235,1128 1245,1140 1245,1310 1235,1320 1162,1320 1162,1390 1055,1430 275,1430 165,1390 165,1320 95,1320 85,1310 85,1140 95,1128 165,1128 165,1058"/>
    <polygon class="cut-outline" points="275,1430 1055,1430 1038,1477 290,1477"/>
    <line class="fold-line" x1="275" y1="92" x2="275" y2="1430"/>
    <line class="fold-line" x1="1055" y1="92" x2="1055" y2="1430"/>
  </g>

  <g class="brand-mark brand-mark--top" transform="rotate(180 668 215)">
    <ellipse class="brand-label" cx="668" cy="215" rx="150" ry="67"/>
    <text class="brand-name" x="668" y="228" font-size="66" text-anchor="middle">Velora</text>
    <text class="brand-descriptor" x="668" y="262" font-size="26" text-anchor="middle">Facial Tissue</text>
  </g>

  <g class="brand-mark brand-mark--front">
    <ellipse class="brand-label" cx="665" cy="557" rx="215" ry="97"/>
    <text class="brand-name" x="665" y="575" font-size="100" text-anchor="middle">Velora</text>
    <text class="brand-descriptor" x="665" y="622" font-size="38" text-anchor="middle">Facial Tissue</text>
  </g>

  <g class="brand-mark brand-mark--bottom">
    <ellipse class="brand-label" cx="668" cy="888" rx="150" ry="67"/>
    <text class="brand-name" x="668" y="901" font-size="66" text-anchor="middle">Velora</text>
    <text class="brand-descriptor" x="668" y="935" font-size="26" text-anchor="middle">Facial Tissue</text>
  </g>
</svg>
</body>
</html>
```